Brisk Fixwell business card

I need business card for my business, I think you have all my details.six months ago I design with you car wrap design. We would like to design both side of the card. On front of card we would like logo , Name and our contact details.
At the back we are looking to mentioned our services.
The name will be:
Faridoullan Mestor
Managing Director
Ph:07952338417
Email:info@brisk-fixwell.com
Web:www.brisk-fixwell.com
So we have our logo, you don’t need to change the logo.
Please see the attachment.
Thanks

Target Market(s)

Home improvement

Industry/Entity Type

Home Improvement

Contact Information for Business Card

Company name: Brisk Fixwell
Name: Faridoullan Mestor
Position: Director
Ph:07952338417
Web: www.brisk-fixwell.com
Add: 42 Corvale Road
Hounslow
TW3 9KD
SECOND PERSON
Nizamuddel mestor
Position: Handyman
Ph: 07812 564037
Email: info@brisk-fixwell.com
Add: 18 Brackwin Lane Road
Hounslow
TW6 2LB

```html
<!DOCTYPE html>
<html lang="en">
<head>
<meta charset="utf-8">
<title>Brisk Fixwell business card</title>
<link rel="stylesheet" href="https://fonts.googleapis.com/css2?family=Arimo:wght@400;700&display=swap">
<style>
  :root {
    --navy: #233a80;
    --red: #e2202b;
    --grey: #8a8a8a;
    --rule: #d8d8d8;
    --paper: #ffffff;
    --backdrop: #2e2e30;
  }
  * { box-sizing: border-box; margin: 0; padding: 0; }
  html, body { width: 1200px; height: 866px; overflow: hidden; }
  body {
    background: var(--backdrop);
    font-family: "Arimo", Arial, sans-serif;
    display: flex;
    flex-direction: column;
    align-items: center;
    justify-content: center;
    gap: 28px;
  }
  .card {
    width: 680px;
    height: 389px;
    position: relative;
    overflow: hidden;
  }
  /* Front */
  .card-front { background: var(--paper); color: var(--navy); }
  .holder { position: absolute; left: 44px; top: 104px; }
  .holder-name {
    font-weight: 700; font-size: 21px; letter-spacing: 1.5px; text-transform: uppercase;
  }
  .holder-role {
    font-size: 14px; letter-spacing: 1.5px; color: var(--grey); text-transform: uppercase; margin-top: 2px;
  }
  .contact-list { list-style: none; margin-top: 26px; }
  .contact-list li {
    display: flex; align-items: center; gap: 10px;
    font-size: 15px; letter-spacing: 0.6px; color: #444; line-height: 23px;
  }
  .contact-list li.web { color: var(--navy); }
  .contact-list svg { width: 14px; height: 14px; flex: none; }
  .brand {
    position: absolute; right: 44px; top: 118px;
    display: flex; align-items: center; gap: 14px;
  }
  .brand-name {
    font-weight: 700; font-size: 30px; letter-spacing: 1px; text-transform: uppercase; color: var(--navy);
  }
  .brand-mark { width: 26px; height: 26px; background: var(--red); }
  .rule {
    position: absolute; left: 44px; right: 44px; top: 268px; height: 1px; background: var(--rule);
  }
  .address {
    position: absolute; right: 44px; top: 292px; text-align: right;
    font-size: 16px; letter-spacing: 1px; line-height: 22px; color: #333;
  }
  /* Back */
  .card-back { background: var(--navy); color: #fff; }
  .service-list {
    list-style: none; position: absolute;
  }
  .service-list.col-a { left: 86px; top: 72px; }
  .service-list.col-b { left: 370px; top: 150px; }
  .service-list li {
    display: flex; align-items: center; gap: 14px;
    font-size: 24px; letter-spacing: 1.5px; text-transform: uppercase; line-height: 40px;
  }
  .bullet {
    width: 14px; height: 14px; background: var(--red); border: 2px solid #fff; flex: none;
  }
</style>
</head>
<body>
  <section class="card card-front">
    <div class="holder">
      <p class="holder-name">Faridoullan Mestor</p>
      <p class="holder-role">Director</p>
      <ul class="contact-list">
        <li>
          <svg viewBox="0 0 16 16"><path d="M4 1l3 3-2 2c1 2 3 4 5 5l2-2 3 3-2 3C7 15 1 9 1 3z" fill="var(--navy)"/></svg>
          07952338417
        </li>
        <li>
          <svg viewBox="0 0 16 16"><rect x="1" y="3" width="14" height="10" fill="var(--navy)"/><path d="M1 3l7 6 7-6" stroke="#fff" stroke-width="1.4" fill="none"/></svg>
          info@brisk-fixwell.com
        </li>
        <li class="web">
          <svg viewBox="0 0 16 16" fill="none" stroke="var(--navy)" stroke-width="1.3"><circle cx="8" cy="8" r="6.5"/><ellipse cx="8" cy="8" rx="3" ry="6.5"/><path d="M1.5 8h13M2.5 4.5h11M2.5 11.5h11"/></svg>
          www.brisk-fixwell.com
        </li>
      </ul>
    </div>
    <div class="brand">
      <span class="brand-name">Brisk Fixwell</span>
      <span class="brand-mark"></span>
    </div>
    <div class="rule"></div>
    <p class="address">42 Corvale Road<br>Hounslow, TW3 9KD</p>
  </section>

  <section class="card card-back">
    <ul class="service-list col-a">
      <li><span class="bullet"></span>Plumbing</li>
      <li><span class="bullet"></span>Carpentry</li>
      <li><span class="bullet"></span>Painting</li>
      <li><span class="bullet"></span>Decorating</li>
      <li><span class="bullet"></span>Decking</li>
      <li><span class="bullet"></span>Fence</li>
    </ul>
    <ul class="service-list col-b">
      <li><span class="bullet"></span>Gutter</li>
      <li><span class="bullet"></span>Flooring</li>
      <li><span class="bullet"></span>Plastering</li>
      <li><span class="bullet"></span>Tilling</li>
      <li><span class="bullet"></span>Gardening</li>
    </ul>
  </section>
</body>
</html>
```